The Copper Kite Website Redesign

I want a new design and website for www.thecopperkitebrookvale.com where part of the home page includes our daily specials from our POS Toast to be pulled from API. I have included photos and links to give you a better feel for the style of our restaurant.

Coding

Coded - Design and coding required

```html
<!DOCTYPE html>
<html lang="en">
<head>
<meta charset="utf-8">
<title>The Copper Kite</title>
<link rel="stylesheet" href="https://fonts.googleapis.com/css2?family=Amatic+SC:wght@700&family=Kalam:wght@400;700&family=Montserrat:wght@400;500&display=swap">
<style>
:root{
  --ink:#141414;
  --ink-2:#1d1d1d;
  --slate:#2c2c2c;
  --red:#ee1c1c;
  --orange:#f27a0c;
  --white:#ffffff;
  --text:#5b5b5b;
  --muted:#8a8a8a;
  --line:#e6e6e6;
}
*{margin:0;padding:0;box-sizing:border-box}
html,body{width:1200px;height:3870px;overflow:hidden;background:var(--white)}
body{position:relative;font-family:"Montserrat",sans-serif;color:var(--text)}
.abs{position:absolute}
.hand{font-family:"Kalam",cursive}
.sketch{font-family:"Amatic SC",cursive;font-weight:700}

/* hero */
.hero{left:0;top:0;width:1200px;height:705px;background:radial-gradient(ellipse at 50% 30%,#3a3a3a 0%,#262626 60%,#1b1b1b 100%)}
.hero-food{left:0;top:460px;width:1200px;height:200px;background:linear-gradient(90deg,#7a4a2a 0%,#7c8a3a 18%,#d8d0c0 35%,#b63a2a 55%,#c8c0b0 75%,#4f6a2a 100%);opacity:.55}
.edge{position:absolute;left:0;width:1200px}
.brand{color:var(--white);font-family:"Kalam",cursive;font-weight:700;white-space:nowrap}
.nav{top:52px;left:405px;display:flex;gap:30px;font-size:19px;color:var(--white)}
.nav .on{color:var(--red)}
.phone{top:44px;left:890px;display:flex;align-items:center;gap:12px;color:var(--white);font-size:26px}
.phone-ring{width:48px;height:48px;border-radius:50%;background:var(--white);border:4px solid var(--red);display:flex;align-items:center;justify-content:center}
.welcome{top:160px;width:1200px;text-align:center;color:var(--orange);font-size:54px}
.hero-title{top:240px;width:1200px;text-align:center;font-size:104px}
.arrow{top:292px;width:56px;height:56px;border:3px solid var(--white);border-radius:50%;display:flex;align-items:center;justify-content:center}

/* about */
.about-photo{left:90px;top:748px;width:468px;height:468px;border-radius:50%;border:7px solid var(--orange);background:radial-gradient(circle at 50% 45%,#c99446 0%,#7a4a26 45%,#3d5d2a 70%,#2a3d5a 100%)}
.eyebrow{color:var(--orange);font-size:26px}
.about-title{left:630px;top:780px;font-size:46px;color:#111;font-weight:700}
.about-copy{left:630px;top:858px;width:442px;font-size:15.3px;line-height:23.2px}
.btn{background:var(--red);color:var(--white);border-radius:30px;display:flex;align-items:center;justify-content:center}
.btn-read{left:625px;top:1158px;width:200px;height:57px;font-size:24px;font-family:"Kalam",cursive;font-weight:700}

/* specials */
.specials{left:0;top:1350px;width:1200px;height:1010px;background:var(--ink)}
.sec-head{border-left:3px solid var(--red);padding-left:18px;font-size:44px;line-height:52px}
.sec-sub{font-size:15px}
.card{width:309px;height:350px;border-radius:14px;overflow:hidden}
.card-photo{width:100%;height:100%}
.card-label{position:absolute;bottom:26px;width:100%;text-align:center;color:var(--white);font-size:30px}
.card-menu{background:#1e1e1e;padding:28px 40px;color:var(--white);font-size:15.5px;line-height:26px}
.card-menu h4{font-family:"Amatic SC",cursive;font-size:32px;margin-bottom:14px;font-weight:700}
.card-menu .dish{color:var(--red);font-size:17px;font-weight:500}

/* retail */
.r-card{width:314px;height:410px;border-radius:14px;background:var(--white);box-shadow:0 6px 18px rgba(0,0,0,.1);overflow:hidden}
.r-photo{height:222px}
.r-body{padding:20px 24px}
.r-date{font-size:13px;color:#444;display:flex;align-items:center;gap:8px;font-family:"Kalam",cursive}
.r-title{font-size:38px;color:#111;margin:6px 0 14px}
.r-copy{font-size:13px;line-height:19px;color:var(--muted)}

/* footer */
.footer{left:0;top:3230px;width:1200px;height:640px;background:var(--ink)}
.foot-nav{top:3600px;left:111px;width:977px;height:66px;border-top:3px solid #555;border-bottom:3px solid #555;display:flex;justify-content:center;align-items:center;gap:44px;color:var(--white);font-size:24px}
.social{top:3708px;left:500px;display:flex;gap:8px}
.social span{width:34px;height:34px;border-radius:50%;border:2px solid var(--white)}
.social span.first{border-color:var(--red)}
.copyright{top:3807px;width:1200px;text-align:center;color:var(--white);font-size:15px}
</style>
</head>
<body>

<section class="hero abs" role="img" aria-label="Dark slate tabletop background"></section>
<div class="hero-food abs" role="img" aria-label="Row of dishes, avocado, chopsticks and sauces along the bottom of the slate"></div>
<svg class="edge" style="top:600px" width="1200" height="110" viewBox="0 0 1200 110" aria-hidden="true">
  <path d="M0 40 L60 55 L120 35 L200 60 L280 40 L360 58 L450 38 L540 62 L630 42 L720 60 L810 36 L900 58 L990 40 L1080 62 L1150 44 L1200 52 L1200 110 L0 110 Z" fill="#fff"/>
</svg>

<div class="brand abs" style="top:30px;left:110px;font-size:38px">The Copper Kite</div>
<nav class="nav abs hand">
  <span class="on">Home</span><span>About Us</span><span>Menu</span><span>Retail</span><span>Press</span><span>Contact Us</span>
</nav>
<div class="phone abs hand">
  <div class="phone-ring">
    <svg width="24" height="24" viewBox="0 0 24 24"><path d="M6.6 10.8a15 15 0 0 0 6.6 6.6l2.2-2.2a1 1 0 0 1 1-.25 11.4 11.4 0 0 0 3.6.57 1 1 0 0 1 1 1V20a1 1 0 0 1-1 1A17 17 0 0 1 3 4a1 1 0 0 1 1-1h3.5a1 1 0 0 1 1 1c0 1.25.2 2.45.57 3.6a1 1 0 0 1-.25 1z" fill="none" stroke="#111" stroke-width="1.6"/></svg>
  </div>
  <span>555-014-2290</span>
</div>
<div class="welcome abs sketch">Welcome To</div>
<div class="hero-title abs brand">The Copper Kite</div>
<div class="arrow abs" style="left:43px"><svg width="28" height="28" viewBox="0 0 28 28"><path d="M24 14H5M13 6l-8 8 8 8" fill="none" stroke="#fff" stroke-width="3"/></svg></div>
<div class="arrow abs" style="left:1093px"><svg width="28" height="28" viewBox="0 0 28 28"><path d="M4 14h19M15 6l8 8-8 8" fill="none" stroke="#fff" stroke-width="3"/></svg></div>

<section>
  <div class="about-photo abs" role="img" aria-label="Stacked cheeseburger on a diner plate"></div>
  <div class="eyebrow abs sketch" style="left:630px;top:735px">About Us</div>
  <h2 class="about-title abs hand">Copper Kite Fodder</h2>
  <p class="about-copy abs">The doors of The Copper Kite: a finer diner were eagerly thrown open for the first time on December 28th 2004. We welcomed our first customers and started our magnificent life as a business that continues on through today. Along with our beloved and inquisitive customers came the many questions of our origin. The most important of which we will address right here and now... "Why?" they asked "Why did you name your restaurant The Copper Kite?" We always swore we would make up some exciting folklore tale of the origin of our now-venerated name, but we never quite came up with a story glorious enough to do justice to the wonderment.</p>
  <div class="btn btn-read abs">Read More</div>
</section>

<section>
  <svg class="edge" style="top:1310px" width="1200" height="60" viewBox="0 0 1200 60" aria-hidden="true">
    <path d="M0 45 L80 28 L160 40 L250 18 L340 36 L430 22 L520 38 L610 20 L700 34 L790 16 L880 32 L970 14 L1060 30 L1140 18 L1200 26 L1200 60 L0 60 Z" fill="#141414"/>
  </svg>
  <div class="specials abs"></div>
  <svg class="edge" style="top:2330px" width="1200" height="60" viewBox="0 0 1200 60" aria-hidden="true">
    <path d="M0 0 L1200 0 L1200 20 L1110 36 L1020 24 L930 42 L840 28 L750 44 L660 30 L570 46 L480 30 L390 44 L300 28 L210 40 L120 26 L40 38 L0 30 Z" fill="#141414"/>
  </svg>

  <h2 class="sec-head abs sketch" style="left:121px;top:1386px;color:#fff">Our Daily <span style="color:var(--red)">Specials</span></h2>
  <p class="sec-sub abs" style="left:143px;top:1458px;color:#fff">Sed ut perspiciatis unde omnis iste natus error sit voluptatem</p>
  <div class="btn abs hand" style="left:928px;top:1420px;width:149px;height:43px;font-size:16px;font-weight:700">View All Specials</div>

  <div class="card abs" style="left:111px;top:1532px">
    <div class="card-photo" role="img" aria-label="Deviled eggs and smoked salmon bites" style="background:linear-gradient(160deg,#8a5a3a,#c8884a 50%,#5a3a26)"></div>
    <div class="card-label sketch">All Things Eggs</div>
  </div>
  <div class="card card-menu abs" style="left:445px;top:1532px">
    <h4>Oh, Sugar Shack!</h4>
    <div class="dish">Gingerbread Waffle :</div>
    <div>with Sautéed Apples, Cherries &amp; Cinnamon Syrup $10.95</div>
    <div class="dish" style="margin-top:14px">Granola :</div>
    <div>House Mixed Nuts, Seeds &amp; Honey Rolled Oats, with Coconut, Banana &amp; Vanilla Yogurt $9.95</div>
  </div>
  <div class="card abs" style="left:779px;top:1532px">
    <div class="card-photo" role="img" aria-label="Roasted potatoes with spinach and eggs" style="background:linear-gradient(160deg,#6a4a2a,#a86a2a 45%,#3a4a26)"></div>
    <div class="card-label sketch">Green Things</div>
  </div>
  <div class="card abs" style="left:111px;top:1910px">
    <div class="card-photo" role="img" aria-label="Chicken salad sandwich on toasted bread" style="background:linear-gradient(170deg,#c8a070,#d8d0c0 50%,#6a7a3a)"></div>
    <div class="card-label sketch">Between Bread</div>
  </div>
  <div class="card abs" style="left:445px;top:1910px">
    <div class="card-photo" role="img" aria-label="Roast turkey platter" style="background:linear-gradient(160deg,#4a5a3a,#8a5a2a 50%,#3a2a1a)"></div>
    <div class="card-label sketch">Other Stuff</div>
  </div>
  <div class="card abs" style="left:779px;top:1910px">
    <div class="card-photo" role="img" aria-label="Braided challah loaf" style="background:linear-gradient(160deg,#5a7aa0,#d89a4a 45%,#c07a3a)"></div>
    <div class="card-label sketch">Other Whistle Wetters</div>
  </div>
</section>

<section>
  <h2 class="sec-head abs sketch" style="left:113px;top:2500px;color:#111">Our <span style="color:var(--red)">Retail</span></h2>
  <p class="sec-sub abs" style="left:135px;top:2572px">Sed ut perspiciatis unde omnis iste natus error sit voluptatem</p>
  <div class="btn abs" style="left:872px;top:2527px;width:213px;height:46px;font-size:18px">View All Events</div>

  <article class="r-card abs" style="left:111px;top:2648px">
    <div class="r-photo" role="img" aria-label="Three bottles of hot sauce" style="background:linear-gradient(90deg,#8a8a2a,#4a6a2a 50%,#b0301a)"></div>
    <div class="r-body">
      <div class="r-date"><svg width="14" height="14" viewBox="0 0 14 14"><rect x="1" y="2" width="12" height="11" fill="none" stroke="#ee1c1c" stroke-width="1.5"/><path d="M1 6h12M4 0v4M10 0v4" stroke="#ee1c1c" stroke-width="1.5"/></svg>02 Jan 2025</div>
      <div class="r-title sketch">Zap Sauces</div>
      <p class="r-copy">Lorem ipsum dolor sit amet, consectetur adipiscing elit, sed do eiusmod tempor incididunt ut labore</p>
    </div>
  </article>
  <article class="r-card abs" style="left:442px;top:2648px">
    <div class="r-photo" role="img" aria-label="Table spread of festive dishes" style="background:radial-gradient(circle,#9a1a2a 0%,#6a3a2a 45%,#2a3a22 100%)"></div>
    <div class="r-body">
      <div class="r-date"><svg width="14" height="14" viewBox="0 0 14 14"><rect x="1" y="2" width="12" height="11" fill="none" stroke="#ee1c1c" stroke-width="1.5"/><path d="M1 6h12M4 0v4M10 0v4" stroke="#ee1c1c" stroke-width="1.5"/></svg>02 Jan 2025</div>
      <div class="r-title sketch">Gift Card</div>
      <p class="r-copy">Lorem ipsum dolor sit amet, consectetur adipiscing elit, sed do eiusmod tempor incididunt ut labore</p>
    </div>
  </article>
  <article class="r-card abs" style="left:773px;top:2648px">
    <div class="r-photo" role="img" aria-label="Printed restaurant t-shirt" style="background:linear-gradient(90deg,#d8d4cc,#f2f0ec 50%,#cfcac2)"></div>
    <div class="r-body">
      <div class="r-date"><svg width="14" height="14" viewBox="0 0 14 14"><rect x="1" y="2" width="12" height="11" fill="none" stroke="#ee1c1c" stroke-width="1.5"/><path d="M1 6h12M4 0v4M10 0v4" stroke="#ee1c1c" stroke-width="1.5"/></svg>02 Jan 2025</div>
      <div class="r-title sketch">T-Shirts</div>
      <p class="r-copy">Lorem ipsum dolor sit amet, consectetur adipiscing elit, sed do eiusmod tempor incididunt ut labore</p>
    </div>
  </article>
</section>

<footer>
  <svg class="edge" style="top:3160px" width="1200" height="80" viewBox="0 0 1200 80" aria-hidden="true">
    <path d="M0 20 L90 34 L180 14 L270 36 L360 18 L450 40 L540 20 L630 38 L720 16 L810 36 L900 18 L990 40 L1080 22 L1200 34 L1200 80 L0 80 Z" fill="#141414"/>
  </svg>
  <div class="footer abs"></div>
  <div class="brand abs" style="top:3380px;width:1200px;text-align:center;font-size:88px">The Copper Kite</div>
  <nav class="foot-nav abs hand">
    <span>Home</span><span>About Us</span><span>Menu</span><span>Retail</span><span>Press</span><span>Contact Us</span>
  </nav>
  <div class="social abs"><span class="first"></span><span></span><span></span><span></span><span></span></div>
  <p class="copyright abs">copyright © 2025 Company Name. all rights reserved</p>
</footer>

</body>
</html>
```